Flag Order

We were just looking to order some branding flags to put on our rental equipment for our business. We would like different examples of the colors, shapes, sizes, backgrounds etc. Was thinking of just doing the plains icon instead of the whole logo on there. but open to ideas. preferably not a white background as they could get dirty,

```html
<!DOCTYPE html>
<html lang="en">
<head>
<meta charset="utf-8">
<title>Kestrel Tool Hire – Equipment Flag</title>
<link rel="stylesheet" href="https://fonts.googleapis.com/css2?family=Oswald:wght@500&display=swap">
<style>
  :root {
    --stage: #666666;
    --flag-blue: #009be5;
    --flag-white: #ffffff;
    --flag-black: #2a2a2a;
    --ink: #2a2a2a;
  }
  html, body {
    margin: 0;
    padding: 0;
    width: 1200px;
    height: 1200px;
    overflow: hidden;
    background: var(--stage);
  }
  .canvas {
    width: 1200px;
    height: 1200px;
    display: flex;
    align-items: center;
    justify-content: center;
  }
  .flag {
    width: 376px;
    height: 1060px;
    display: block;
  }
  .brand-name {
    font-family: "Oswald", sans-serif;
    font-weight: 500;
    fill: var(--ink);
  }
  .phone {
    font-family: "Oswald", sans-serif;
    font-weight: 500;
    fill: var(--flag-white);
  }
  .web {
    font-family: "Oswald", sans-serif;
    font-weight: 500;
    fill: var(--flag-blue);
  }
</style>
</head>
<body>
  <main class="canvas">
    <svg class="flag" viewBox="0 0 250 705" aria-label="Kestrel Tool Hire equipment flag">
      <rect class="flag-blue-field" x="0" y="0" width="127" height="705" fill="var(--flag-blue)"/>
      <rect class="flag-white-strip" x="127" y="0" width="123" height="705" fill="var(--flag-white)"/>
      <polygon class="flag-black-corner" points="0,495 250,620 250,705 0,705" fill="var(--flag-black)"/>

      <rect class="brand-square" x="168" y="450" width="36" height="36" fill="var(--flag-blue)"/>

      <g transform="translate(200 425) rotate(-90)">
        <text class="brand-name" x="0" y="0" font-size="34" textLength="330" lengthAdjust="spacing">KESTREL TOOL HIRE</text>
      </g>

      <text class="phone" x="125" y="662" font-size="32" text-anchor="middle" textLength="198" lengthAdjust="spacingAndGlyphs">555-010-4827</text>
      <text class="web" x="125" y="690" font-size="14" text-anchor="middle" textLength="196" lengthAdjust="spacingAndGlyphs">KESTRELTOOLHIRE.COM</text>
    </svg>
  </main>
</body>
</html>
```